Veldmark Supplies Business Card

Professional business card that stand out to our potential customers. Front and back with clean modern design

Industry/Entity Type

Oil and gas

Contact Information for Business Card

Name, address, website , office phone and cell number

Requirements
Must have
• Editable files for each employee

```html
<!DOCTYPE html>
<html lang="en">
<head>
<meta charset="utf-8">
<title>Veldmark Supplies – Business Card</title>
<link href="https://fonts.googleapis.com/css2?family=Arimo:wght@400;700&display=swap" rel="stylesheet">
<style>
  :root {
    --stage: #3d3d3d;
    --card-dark: #2e2e2e;
    --brand-blue: #05b0d3;
    --brand-red: #ff0000;
    --white: #ffffff;
    --card-w: 520px;
    --card-h: 300px;
  }
  * { box-sizing: border-box; margin: 0; padding: 0; }
  html, body { width: 1200px; height: 803px; overflow: hidden; }
  body {
    background: var(--stage);
    font-family: "Arimo", Arial, sans-serif;
    position: relative;
  }
  .card {
    position: absolute;
    top: 252px;
    width: var(--card-w);
    height: var(--card-h);
    border-radius: 22px;
    overflow: hidden;
    box-shadow: 0 18px 40px rgba(0,0,0,.35);
  }
  /* Front */
  .card--front { left: 50px; background: var(--brand-blue); }
  .front__panel {
    position: absolute; inset: 0;
    background: var(--white);
    clip-path: polygon(66% 0, 100% 0, 100% 100%, 52% 100%);
  }
  .front__mark {
    position: absolute; right: 34px; top: 104px;
    width: 150px; text-align: center;
  }
  .mark-square {
    display: block; width: 34px; height: 34px;
    background: var(--brand-red); margin: 0 auto 12px;
  }
  .mark-name {
    font-weight: 700; font-size: 22px; line-height: 1.1;
    color: var(--brand-red); letter-spacing: .5px;
  }
  .front__info { position: absolute; left: 34px; top: 36px; color: var(--white); }
  .front__brand {
    font-weight: 700; font-size: 17px; letter-spacing: 1px;
    text-transform: uppercase; color: var(--white); margin-bottom: 20px;
  }
  .person__name { font-weight: 700; font-size: 24px; color: var(--brand-red); line-height: 1; }
  .person__title { font-size: 12px; margin-top: 3px; }
  .address { font-size: 13px; line-height: 1.3; margin-top: 18px; }
  .contacts { list-style: none; margin-top: 14px; font-size: 13px; line-height: 1.45; }
  .contacts li { display: flex; align-items: center; gap: 8px; }
  .contacts svg { width: 12px; height: 12px; flex: none; }
  /* Back */
  .card--back { left: 630px; background: var(--card-dark); }
  .back__mark {
    position: absolute; inset: 0;
    display: flex; flex-direction: column; align-items: center; justify-content: center;
  }
  .back__mark .mark-square { width: 46px; height: 46px; margin-bottom: 18px; }
  .back__mark .mark-name { font-size: 28px; text-transform: uppercase; letter-spacing: 2px; }
</style>
</head>
<body>
  <article class="card card--front" aria-label="Business card front">
    <div class="front__panel"></div>
    <div class="front__mark">
      <span class="mark-square"></span>
      <p class="mark-name">Veldmark Supplies</p>
    </div>
    <div class="front__info">
      <p class="front__brand">Veldmark Supplies</p>
      <p class="person__name">Dana Whitlow</p>
      <p class="person__title">President</p>
      <p class="address">4120 Larkspur Road<br>Calder Bay, Canada 58213</p>
      <ul class="contacts">
        <li><svg viewBox="0 0 12 12" aria-hidden="true"><path d="M2 1h3l1 3-2 1a7 7 0 0 0 3 3l1-2 3 1v3c-6 0-9-3-9-9z" fill="var(--brand-red)"/></svg>555-210-4817</li>
        <li><svg viewBox="0 0 12 12" aria-hidden="true"><rect x="3" y="1" width="6" height="10" rx="1" fill="none" stroke="var(--brand-red)" stroke-width="1.5"/></svg>555-392-6605</li>
        <li><svg viewBox="0 0 12 12" aria-hidden="true"><rect x="1" y="2.5" width="10" height="7" fill="var(--brand-red)"/><path d="M1 2.5l5 4 5-4" fill="none" stroke="var(--white)" stroke-width="1"/></svg>info@veldmarksupplies.com</li>
        <li><svg viewBox="0 0 12 12" aria-hidden="true"><circle cx="6" cy="6" r="5" fill="var(--brand-red)"/><path d="M1 6h10M6 1c-2 3-2 7 0 10M6 1c2 3 2 7 0 10" fill="none" stroke="var(--white)" stroke-width=".8"/></svg>www.veldmarksupplies.com</li>
      </ul>
    </div>
  </article>

  <article class="card card--back" aria-label="Business card back">
    <div class="back__mark">
      <span class="mark-square"></span>
      <p class="mark-name">Veldmark Supplies</p>
    </div>
  </article>
</body>
</html>
```